Business Cards for new orthopaedic surgery practice

My husband and I are starting our own orthopaedic surgery practice. We are looking for a business card that is uniform, but one will have my name/title and the other will have his. You can just create one design with my name on it for now. But when I choose your design as the winning design I will ask that you add another copy with his name/title.

We are looking for classy, simple, elite all in one. We like dark blues/a little gold/yellow. Something that goes with our logo. We want our logo incorporated. Here is all the info you need:
Business name: RV Bone & Vitality Center
Location: 38517 North Willowmere Ave
Maple Hollow, FL 34819
Phone: 954-218-4063
Fax: 954-582-7341
Email: info@myrvbonecare.example

Names: Lydia Vance, M.D.
Board Certified Hand and Upper Extremity Surgeon

Ebo Dansu, M.D.
Board Certified Hip & Knee Replacement/General Orthopaedic Surgeon

Can decide what you want to put on the back. Maybe a slogan:
Steady Hands. Lasting Strength

I am just going to upload our logo. The only thing is if we select you as the winning design, the location, and phone numbers may change. We will need your help to update that once fully solidified.

Industry/Entity Type

Medical

Contact Information for Business Card

Colors
0054AA
0677BA
7BADD7
CADEEF
E8F1F8
0094D4
00A9DD
6FCCEA
C7EBF8
E9F6FB

Requirements
Must have
• class, appeal,
Should not have
• We want to air on the side of masculine if we are looking at masculine vs. feminine feel. But we still want it classy, sophisticated, and something we will love

```html
<!DOCTYPE html>
<html lang="en">
<head>
<meta charset="utf-8">
<title>RV Bone &amp; Vitality Center — Business Card</title>
<link href="https://fonts.googleapis.com/css2?family=Libre+Baskerville:wght@400;700&family=PT+Serif:wght@400;700&display=swap" rel="stylesheet">
<style>
  :root {
    --navy: #1b2a4e;
    --gold: #c6a35c;
    --ink: #55585e;
    --paper: #ffffff;
    --paper-shade: #eeeff1;
    --backdrop: #2e2f31;
    --ghost: #dfe2e7;
  }
  * { box-sizing: border-box; margin: 0; padding: 0; }
  html, body { width: 1200px; height: 900px; overflow: hidden; }
  body {
    background: var(--backdrop);
    font-family: "PT Serif", Georgia, serif;
    position: relative;
  }
  .card {
    position: absolute;
    left: 290px;
    width: 620px;
    height: 354px;
    background: linear-gradient(135deg, var(--paper) 40%, var(--paper-shade) 100%);
    overflow: hidden;
  }
  .card--back { top: 60px; }
  .card--front { top: 480px; }

  .brand {
    display: flex;
    align-items: center;
    gap: 10px;
    font-family: "Libre Baskerville", Georgia, serif;
    font-weight: 700;
    color: var(--navy);
    line-height: 1.25;
  }
  .brand__dot {
    width: 14px; height: 14px; border-radius: 50%;
    background: var(--gold);
    flex: none;
  }

  /* back */
  .card--back .brand {
    position: absolute; left: 0; right: 0; top: 96px;
    justify-content: center; font-size: 22px;
  }
  .card--back .rule {
    position: absolute; left: 70px; right: 70px; top: 200px;
    height: 1px;
    background: linear-gradient(90deg, transparent, var(--gold) 20%, var(--gold) 80%, transparent);
  }
  .tagline {
    position: absolute; left: 0; right: 0; top: 222px;
    text-align: center;
    font-family: "Libre Baskerville", Georgia, serif;
    font-weight: 700; font-size: 19px; color: var(--navy);
  }

  /* front */
  .card--front .brand {
    position: absolute; left: 36px; top: 40px; font-size: 17px; width: 220px;
  }
  .ghost-mark {
    position: absolute; right: 36px; top: 28px;
    font-family: "Libre Baskerville", Georgia, serif;
    font-weight: 700; font-size: 28px; line-height: 1.15;
    color: var(--ghost); text-align: right;
  }
  .name-row {
    position: absolute; left: 36px; right: 36px; top: 150px;
    display: flex; align-items: baseline; gap: 10px;
  }
  .name {
    font-family: "Libre Baskerville", Georgia, serif;
    font-weight: 700; font-size: 21px; color: var(--navy); white-space: nowrap;
  }
  .name-row__line { flex: 1; height: 1.5px; background: var(--navy); }
  .title {
    position: absolute; left: 36px; top: 180px;
    font-size: 16px; color: var(--ink);
  }
  .contact {
    position: absolute; left: 58px; top: 218px;
    list-style: none; font-size: 16px; color: var(--ink);
  }
  .contact li { display: flex; align-items: center; gap: 12px; height: 26px; }
  .contact svg { width: 15px; height: 15px; fill: var(--gold); flex: none; }
</style>
</head>
<body>

<section class="card card--back">
  <div class="brand"><span class="brand__dot"></span>RV Bone &amp; Vitality Center</div>
  <div class="rule"></div>
  <p class="tagline">Steady Hands. Lasting Strength</p>
</section>

<section class="card card--front">
  <div class="ghost-mark" aria-hidden="true">RV Bone &amp;<br>Vitality<br>Center</div>
  <div class="brand"><span class="brand__dot"></span>RV Bone &amp; Vitality Center</div>

  <div class="name-row">
    <span class="name">Lydia Vance, M.D.</span>
    <span class="name-row__line"></span>
  </div>
  <p class="title">Board Certified Hand and Upper Extremity Surgeon</p>

  <ul class="contact">
    <li>
      <svg viewBox="0 0 24 24" aria-label="Phone"><path d="M6.6 10.8a15.1 15.1 0 0 0 6.6 6.6l2.2-2.2a1 1 0 0 1 1-.25 11.4 11.4 0 0 0 3.6.57 1 1 0 0 1 1 1V20a1 1 0 0 1-1 1A17 17 0 0 1 3 4a1 1 0 0 1 1-1h3.5a1 1 0 0 1 1 1c0 1.25.2 2.45.57 3.57a1 1 0 0 1-.25 1z"/></svg>
      954-218-4063
    </li>
    <li>
      <svg viewBox="0 0 24 24" aria-label="Fax"><path d="M7 3h10v5H7zM4 9h16a2 2 0 0 1 2 2v6h-4v4H6v-4H2v-6a2 2 0 0 1 2-2zm4 7v3h8v-3z"/></svg>
      954-582-7341
    </li>
    <li>
      <svg viewBox="0 0 24 24" aria-label="Email"><path d="M2 5h20v14H2zm2 2v.5l8 5.5 8-5.5V7l-8 5.5z"/></svg>
      info@myrvbonecare.example
    </li>
    <li>
      <svg viewBox="0 0 24 24" aria-label="Address"><path d="M12 2a7 7 0 0 0-7 7c0 5 7 13 7 13s7-8 7-13a7 7 0 0 0-7-7zm0 9.5A2.5 2.5 0 1 1 12 6.5a2.5 2.5 0 0 1 0 5z"/></svg>
      38517 North Willowmere Ave, Maple Hollow, FL 34819
    </li>
  </ul>
</section>

</body>
</html>
```